Creative Law Firm Business Card

attached are photos of myself and our office as well as language that I would like to see on the card, likely on the back, although I leave that to the designer. I have also attached copies of both sides of a marketing card that we produced just for ideas. I would like to find a tactful way to get my photo in along with the office. I attached copies of our logo, both normal and inverted.

I listed my name as Tom Halloway to be casual, however, it should probably read Thomas J Halloway

Requirements
Must have
• attached file #8 has content.
• I would like my picture and the office photo on page 1
• The text, with the exception of the firm name "HALLOWAY & PEMBER" and the firm description underneath it "THE BUSINESS AND BANKRUPTCY LAWYERS", should be on the back. The layout and fonts are up to the designer

```html
<!DOCTYPE html>
<html lang="en">
<head>
<meta charset="UTF-8">
<title>Halloway &amp; Pember — Business Card</title>
<link href="https://fonts.googleapis.com/css2?family=Cinzel:wght@400;600&family=Open+Sans:wght@400&display=swap" rel="stylesheet">
<style>
  :root {
    --backdrop: #d9d9d9;
    --card-white: #ffffff;
    --navy: #1f2f5c;
    --band-blue: #7aaee3;
    --text-dark: #2b2b2b;
    --sky-top: #2f5fc8;
    --sky-low: #6f9be0;
    --facade: #d9c7a6;
    --foliage: #3f5a2c;
    --suit: #1c1c1f;
    --portrait-light: #c9b49d;
  }
  * { box-sizing: border-box; margin: 0; padding: 0; }
  html, body { width: 1200px; height: 852px; overflow: hidden; }
  body {
    background: var(--backdrop);
    display: flex;
    align-items: center;
    justify-content: center;
    gap: 44px;
    font-family: "Open Sans", Arial, sans-serif;
  }
  .card {
    position: relative;
    width: 520px;
    height: 297px;
    border-radius: 14px;
    overflow: hidden;
    box-shadow: 0 4px 14px rgba(0,0,0,0.18);
  }

  /* Front: office and portrait together */
  .card-front .office-photo {
    position: absolute; inset: 0;
    background: linear-gradient(160deg, var(--sky-top) 0%, var(--sky-low) 38%, var(--facade) 62%, #b9a888 82%, var(--foliage) 100%);
  }
  .card-front .firm-heading {
    position: absolute;
    left: 28px; top: 24px;
    color: var(--card-white);
  }
  .card-front .firm-title {
    font-family: "Cinzel", "Times New Roman", serif;
    font-weight: 400;
    font-size: 38px;
    letter-spacing: 1px;
    line-height: 1.1;
    white-space: nowrap;
  }
  .card-front .firm-tagline {
    font-family: "Cinzel", "Times New Roman", serif;
    font-size: 12px;
    letter-spacing: 2px;
    margin-top: 6px;
  }
  .card-front .portrait-photo {
    position: absolute;
    right: 28px; bottom: 0;
    width: 180px; height: 180px;
    background: linear-gradient(180deg, var(--portrait-light) 0%, #a99178 40%, var(--suit) 62%, var(--suit) 100%);
    border-radius: 90px 90px 0 0;
    border: 3px solid var(--card-white);
    border-bottom: none;
  }

  /* Back: details */
  .card-back { background: var(--card-white); }
  .card-back .bottom-band {
    position: absolute; left: 0; right: 0; bottom: 0;
    height: 16px;
    background: var(--band-blue);
  }
  .card-back .details {
    position: absolute;
    left: 44px; top: 38px;
    width: 432px;
  }
  .card-back .brand-rule {
    height: 1px; background: var(--navy);
    margin-left: 30px; margin-bottom: 8px;
  }
  .card-back .brand-row { display: flex; align-items: center; gap: 8px; }
  .card-back .brand-square {
    width: 22px; height: 22px; background: var(--navy); flex: none;
  }
  .card-back .brand-name {
    font-family: "Cinzel", "Times New Roman", serif;
    font-size: 18px; color: var(--navy); white-space: nowrap;
  }
  .card-back .person {
    margin-top: 30px;
    color: var(--navy);
  }
  .card-back .person-name {
    font-family: "Cinzel", "Times New Roman", serif;
    font-size: 17px; letter-spacing: 0.5px;
  }
  .card-back .person-title { font-size: 11px; margin-top: 2px; }
  .card-back .contacts {
    margin-top: 22px;
    list-style: none;
    font-size: 12px; color: var(--text-dark);
  }
  .card-back .contacts li {
    display: flex; align-items: center; gap: 8px; line-height: 21px;
  }
  .card-back .contacts svg { width: 10px; height: 10px; fill: var(--navy); flex: none; }
</style>
</head>
<body>
  <section class="card card-front">
    <div class="office-photo" role="img" aria-label="Photo of the firm's office building with palm trees under a blue sky"></div>
    <div class="firm-heading">
      <h1 class="firm-title">HALLOWAY &amp; PEMBER</h1>
      <p class="firm-tagline">THE BUSINESS AND BANKRUPTCY LAWYERS</p>
    </div>
    <div class="portrait-photo" role="img" aria-label="Portrait photo of the lawyer in a dark suit and tie"></div>
  </section>

  <section class="card card-back">
    <div class="bottom-band"></div>
    <div class="details">
      <div class="brand">
        <div class="brand-rule"></div>
        <div class="brand-row">
          <span class="brand-square"></span>
          <span class="brand-name">HALLOWAY &amp; PEMBER</span>
        </div>
      </div>

      <div class="person">
        <div class="person-name">THOMAS J HALLOWAY</div>
        <div class="person-title">Lawyer</div>
      </div>

      <ul class="contacts">
        <li>
          <svg viewBox="0 0 10 10" aria-hidden="true"><path d="M1 3 Q5 0 9 3 L8 4.5 L6.5 3.8 L6.5 3 Q5 2.5 3.5 3 L3.5 3.8 L2 4.5 Z M2 5 H8 L9 9 H1 Z"/></svg>
          949-555-0186
        </li>
        <li>
          <svg viewBox="0 0 10 10" aria-hidden="true"><path d="M0 2 H10 V8 H0 Z"/><path d="M0 2 L5 6 L10 2" fill="none" stroke="#fff" stroke-width="1"/></svg>
          lawyer@hallowaypember.com
        </li>
        <li>
          <svg viewBox="0 0 10 10" aria-hidden="true"><circle cx="5" cy="5" r="4.5"/><path d="M0.5 5 H9.5 M5 0.5 V9.5" stroke="#fff" stroke-width="0.8"/></svg>
          www.hallowaypember.com
        </li>
      </ul>
    </div>
  </section>
</body>
</html>
```